Velk Partners Building Business Cards

We need a business card that reflects our business as "Solar Experts" in San Diego. Browse our website www.velkpartners.example our License needs to be displayed as "CSLB# 3867140" our phone number is (619) 555-0187

Save thousands on your electric bills and increase the value of your home while helping to protect the environment. Our solar installation experts will help you design the system that's right for you, using only the highest quality equipment that will look great and give you ideal performance. Our goal is to make you energy independent, and get your electric bill to 0.

Paul Osterby
(619) 555-0187
paul@velkpartners.example

Target Market(s)

Home owners in san diego looking for solar

Industry/Entity Type

Solar Energy

Contact Information for Business Card

Paul Osterby
(619) 555-0187
paul@velkpartners.example

Font styles to use
Other font styles liked:
• Use our logo font

Requirements
Must have
• License needs to be displayed as "CSLB# 3867140" our phone number is (619) 555-0187
Nice to have
• Real images of rooftop home solar in san diego
Should not have
• our business address

```html
<!DOCTYPE html>
<html lang="en">
<head>
<meta charset="utf-8">
<title>Velk Partners Building – Business Cards</title>
<link href="https://fonts.googleapis.com/css2?family=Open+Sans:wght@400;600;700&family=Oswald:wght@600&display=swap" rel="stylesheet">
<style>
  :root {
    --navy: #1b4a8c;
    --navy-deep: #163d75;
    --white: #ffffff;
    --gold: #f5a61c;
    --backdrop: #d9dce1;
  }
  html, body {
    margin: 0;
    padding: 0;
    width: 1200px;
    height: 900px;
    overflow: hidden;
    background: var(--backdrop);
    font-family: "Open Sans", Arial, sans-serif;
  }
  .stage {
    position: relative;
    width: 1200px;
    height: 900px;
  }
  .card {
    position: absolute;
    border-radius: 22px;
    overflow: hidden;
    box-shadow: 0 10px 28px rgba(20, 30, 50, 0.25);
  }

  /* Front card (vertical) */
  .card-front {
    left: 110px;
    top: 140px;
    width: 360px;
    height: 620px;
    background: var(--white);
  }
  .card-front .bands {
    position: absolute;
    inset: 0;
  }
  .front-brand {
    position: absolute;
    left: 0;
    right: 0;
    top: 150px;
    text-align: center;
    display: flex;
    align-items: center;
    justify-content: center;
    gap: 10px;
  }
  .brand-dot {
    width: 16px;
    height: 16px;
    border-radius: 50%;
    background: var(--gold);
    flex: none;
  }
  .front-brand .brand-name {
    font-weight: 700;
    font-size: 25px;
    line-height: 1.15;
    color: var(--navy);
    text-align: left;
  }
  .contact {
    position: absolute;
    left: 40px;
    top: 400px;
    color: var(--white);
  }
  .person-name {
    font-family: "Oswald", "Arial Narrow", sans-serif;
    font-weight: 600;
    font-size: 30px;
    letter-spacing: 0.5px;
    text-transform: uppercase;
    margin: 0 0 14px;
    color: var(--white);
  }
  .person-name .surname { color: var(--gold); }
  .contact-list {
    list-style: none;
    margin: 0;
    padding: 0;
    font-size: 15px;
    line-height: 1.9;
  }
  .contact-list li {
    display: flex;
    align-items: center;
    gap: 10px;
  }
  .contact-list svg { flex: none; }
  .web-accent { color: var(--gold); }
  .license {
    position: absolute;
    left: 40px;
    bottom: 30px;
    color: var(--white);
    font-size: 14px;
    font-weight: 600;
  }

  /* Back card (horizontal) */
  .card-back {
    left: 560px;
    top: 260px;
    width: 560px;
    height: 330px;
    background: linear-gradient(160deg, var(--navy) 0%, var(--navy-deep) 100%);
    display: flex;
    align-items: center;
    justify-content: center;
    gap: 16px;
  }
  .card-back .brand-dot { width: 24px; height: 24px; }
  .card-back .brand-name {
    font-weight: 700;
    font-size: 40px;
    color: var(--white);
    line-height: 1.1;
  }
</style>
</head>
<body>
<main class="stage">

  <section class="card card-front" aria-label="Business card front">
    <svg class="bands" width="360" height="620" viewBox="0 0 360 620" aria-hidden="true">
      <path d="M0 385 Q210 380 360 235 L360 620 L0 620 Z" fill="var(--navy)"/>
      <path d="M0 372 Q205 368 348 225" fill="none" stroke="var(--navy)" stroke-width="7"/>
      <path d="M0 380 Q208 376 355 231" fill="none" stroke="var(--white)" stroke-width="3"/>
    </svg>

    <div class="front-brand">
      <span class="brand-dot" aria-hidden="true"></span>
      <span class="brand-name">Velk Partners<br>Building</span>
    </div>

    <div class="contact">
      <h1 class="person-name">Paul <span class="surname">Osterby</span></h1>
      <ul class="contact-list">
        <li>
          <svg width="14" height="16" viewBox="0 0 14 16" aria-hidden="true"><rect x="2" y="1" width="10" height="14" rx="2" fill="none" stroke="#fff" stroke-width="1.5"/></svg>
          (619) 555-0187
        </li>
        <li>
          <svg width="14" height="12" viewBox="0 0 14 12" aria-hidden="true"><rect x="1" y="1" width="12" height="10" fill="none" stroke="#fff" stroke-width="1.3"/><path d="M1 1 L7 7 L13 1" fill="none" stroke="#fff" stroke-width="1.3"/></svg>
          paul@velkpartners.example
        </li>
        <li>
          <svg width="14" height="14" viewBox="0 0 14 14" aria-hidden="true"><circle cx="7" cy="7" r="6" fill="none" stroke="#fff" stroke-width="1.3"/><ellipse cx="7" cy="7" rx="2.6" ry="6" fill="none" stroke="#fff" stroke-width="1"/><path d="M1 7 H13" stroke="#fff" stroke-width="1"/></svg>
          <span>www.<span class="web-accent">velkpartners</span>.example</span>
        </li>
      </ul>
    </div>

    <p class="license">License-"CSLB# 3867140"</p>
  </section>

  <section class="card card-back" aria-label="Business card back">
    <span class="brand-dot" aria-hidden="true"></span>
    <span class="brand-name">Velk Partners<br>Building</span>
  </section>

</main>
</body>
</html>
```